Rollers & Glides.com

Vertical Business Card with focus on branding with our icon. Information on card will be logo, persons name, position, phone number, email address and website. Use the the name Marcus Pellow, position President, phone number 480.915.2267, email Marcus@rollersandglides-demo.com, website www.rollersandglides-demo.com.

```html
<!DOCTYPE html>
<html lang="en">
<head>
<meta charset="utf-8">
<title>Rollers &amp; Glides.com — Business Card</title>
<link rel="stylesheet" href="https://fonts.googleapis.com/css2?family=Roboto:wght@400&family=Arimo:wght@400;700&display=swap">
<style>
  :root {
    --stage: #2a2a2b;
    --card: #0b0b0c;
    --brand-blue: #3a66c4;
    --ink-light: #e9e9ea;
    --rule: #4a4a4d;
  }
  * { box-sizing: border-box; margin: 0; padding: 0; }
  html, body { width: 1200px; height: 900px; overflow: hidden; }
  body {
    background: var(--stage);
    display: flex;
    align-items: center;
    justify-content: center;
    gap: 40px;
    font-family: "Arimo", Arial, sans-serif;
  }
  .card {
    width: 540px;
    height: 309px;
    background: var(--card);
    position: relative;
    box-shadow: 0 10px 30px rgba(0,0,0,.45);
  }
  .brand {
    display: flex;
    align-items: center;
    color: var(--brand-blue);
    font-family: "Roboto", Arial, sans-serif;
    font-weight: 400;
    white-space: nowrap;
  }
  .brand-dot {
    border-radius: 50%;
    background: var(--brand-blue);
    flex: none;
  }
  /* front side */
  .card-front .brand {
    position: absolute;
    left: 0;
    width: 232px;
    top: 92px;
    flex-direction: column;
    gap: 16px;
    font-size: 16px;
    letter-spacing: 1px;
  }
  .card-front .brand-dot { width: 46px; height: 46px; }
  .divider {
    position: absolute;
    left: 232px;
    top: 62px;
    bottom: 62px;
    width: 1px;
    background: var(--rule);
  }
  .contact {
    position: absolute;
    left: 256px;
    top: 86px;
    right: 16px;
    color: var(--ink-light);
  }
  .person-name {
    color: var(--brand-blue);
    font-weight: 700;
    font-size: 19px;
    text-transform: uppercase;
    letter-spacing: .3px;
    line-height: 1;
  }
  .person-role {
    font-size: 15px;
    margin-top: 4px;
  }
  .contact-list {
    list-style: none;
    margin-top: 20px;
    font-size: 12.5px;
  }
  .contact-list li {
    display: flex;
    align-items: center;
    gap: 8px;
    height: 20px;
    white-space: nowrap;
  }
  .contact-list svg { width: 13px; height: 13px; flex: none; }
  .accent { color: var(--brand-blue); }
  /* back side */
  .card-back {
    display: flex;
    align-items: center;
    justify-content: center;
  }
  .card-back .brand {
    flex-direction: column;
    gap: 22px;
    font-size: 30px;
    letter-spacing: 1.5px;
  }
  .card-back .brand-dot { width: 70px; height: 70px; }
</style>
</head>
<body>
  <section class="card card-front" aria-label="Card front">
    <div class="brand">
      <span class="brand-dot"></span>
      <span class="brand-name">Rollers &amp; Glides.com</span>
    </div>
    <div class="divider"></div>
    <div class="contact">
      <h1 class="person-name">Marcus Pellow</h1>
      <p class="person-role">President</p>
      <ul class="contact-list">
        <li>
          <svg viewBox="0 0 16 16" aria-hidden="true"><path fill="#3a66c4" d="M3.6 1.2l2.3 2.6-1.3 1.6c.9 2 2.4 3.5 4.4 4.5l1.6-1.3 2.6 2.3-1.3 2.4C6.7 13.1 2.9 9.3 1.2 4.1z"/></svg>
          <span>480.915.2267</span>
        </li>
        <li>
          <svg viewBox="0 0 16 16" aria-hidden="true"><rect x="1" y="3" width="14" height="10" fill="#3a66c4"/><path d="M1 3l7 6 7-6" fill="none" stroke="#0b0b0c" stroke-width="1.4"/></svg>
          <span>Marcus@rollersandglides-demo.com</span>
        </li>
        <li>
          <svg viewBox="0 0 16 16" aria-hidden="true" fill="none" stroke="#3a66c4" stroke-width="1.3"><circle cx="8" cy="8" r="6.5"/><ellipse cx="8" cy="8" rx="3" ry="6.5"/><path d="M1.5 8h13M2.6 4.6h10.8M2.6 11.4h10.8"/></svg>
          <span>www.<span class="accent">rollersandglides-demo</span>.com</span>
        </li>
      </ul>
    </div>
  </section>

  <section class="card card-back" aria-label="Card back">
    <div class="brand">
      <span class="brand-dot"></span>
      <span class="brand-name">Rollers &amp; Glides.com</span>
    </div>
  </section>
</body>
</html>
```